Luxury Real Estate Website, Midwest, United States

We need web design services for a luxury website. We need IDX Integration with our MLS. We want this to be a very simple website with amazing graphics. We want it to link up with our Postwing account in order to generate leads through a "More Information" Pop up on the main page. We want the main page to be covered with one large graphic that is a rolling slideshow of active listings of $400,000 and up from the IDX Integration. We need this website to give a very exclusive and sleek look. Lots of black is good... I will upload our logos in Black and Silver. We will also need an "About" page that we are going to call "Qeno Info". We want our graphics to be extremely impressive. Keep in mind, we are a company in the Midwest of the United States, and our real estate has a different look than homes in California or Florida. We need graphics that are realistic for the Midwest, yet still high-end.
Target Market(s)
Luxury Homeowners in the Midwest United States. The graphics needs to be pristine.
Industry/Entity Type
Real Estate
Coding
Coded - Design and coding required
Number of Pages Required
3 page
Requirements
Must have
- Large graphics with IDX Integration. The photos of real estate need to represent real estate that is common in the Midwest, United States. We also need Postwing integration. We need a pop up that is titled "My Free Market Analysis" that makes them fill out a contact form asking for Full Name, Email Address, Phone Number and Address. This needs to be a pop up on the front page and will integrate with our Postwing account. We also need a page called "About Qe No Home". And another page where clients can download informational PDFs. The main component needs to be a front page search engine connected with the IDX to access active listings from our MLS. I attached our logos and a sample front page of a website. I would love for ours to look similar.
Nice to have
- Lake House photos on midwest lakes are a plus.
Should not have
- Should not have clutter. This website needs to be clean, luxurious and exclusive.

```html
<!DOCTYPE html>
<html lang="en">
<head>
<meta charset="utf-8">
<title>Hearthline Realty Group</title>
<link rel="stylesheet" href="https://fonts.googleapis.com/css2?family=Lato:ital,wght@0,300;0,400;0,700;0,900;1,400&display=swap">
<style>
:root{
  --ink:#111216;
  --header-bg:#f3f3f3;
  --page-bg:#e2e3e7;
  --card-bg:#e7e9ee;
  --navy:#2a3448;
  --navy-deep:#1d2435;
  --muted:#5a5f6a;
  --line:#b8bfcc;
  --white:#ffffff;
  --footer-bg:#121214;
  --footer-head:#8d9097;
  --footer-text:#4b4e55;
  --btn:#c4c9d4;
}
*{margin:0;padding:0;box-sizing:border-box}
html,body{width:1200px;height:2586px;overflow:hidden}
body{position:relative;background:var(--page-bg);font-family:'Lato',sans-serif;color:var(--ink)}
.abs{position:absolute}

/* header */
.site-header{position:absolute;left:0;top:0;width:1200px;height:108px;background:var(--header-bg)}
.brand{position:absolute;left:74px;top:38px;font-size:28px;font-weight:400;letter-spacing:1px;color:var(--ink);text-transform:uppercase}
.main-nav{position:absolute;top:28px;left:0;width:1200px;height:44px}
.main-nav a{position:absolute;top:0;height:44px;line-height:44px;font-size:14px;color:var(--ink);text-decoration:none;text-transform:uppercase;letter-spacing:.3px}
.main-nav a.active{background:#b9c0cd;padding:0 17px}

/* hero */
.hero{position:absolute;left:0;top:108px;width:1200px;height:552px;background:linear-gradient(180deg,#4a5367 0%,#3e4658 45%,#3c4a3a 88%,#2f3b2b 100%)}
.hero-title{position:absolute;left:0;top:168px;width:1200px;text-align:center;color:#d9dbe0;font-size:58px;font-weight:700;letter-spacing:2px}
.hero-sub{position:absolute;left:0;top:232px;width:1200px;text-align:center;color:#c8cbd2;font-size:34px;font-weight:700}

/* popup */
.popup{position:absolute;left:343px;top:210px;width:514px;height:411px;background:var(--white);overflow:hidden}
.popup-fade{position:absolute;left:0;top:270px;width:514px;height:141px;background:linear-gradient(180deg,#ffffff 0%,#dfe6ee 45%,#c9d6c9 100%);opacity:.8}
.popup-close{position:absolute;right:12px;top:6px;font-size:24px;font-weight:900;color:var(--ink)}
.popup-title{position:absolute;left:0;top:30px;width:514px;text-align:center;font-size:34px;font-weight:700;color:var(--ink)}
.field{position:absolute;height:37px;border:1px solid #aab2c2;background:var(--white);font-size:12px;line-height:35px;padding-left:12px;text-transform:uppercase;color:var(--ink)}
.submit{position:absolute;left:17px;top:238px;width:479px;height:47px;background:#000;color:var(--white);font-size:18px;font-weight:700;text-align:center;line-height:47px;letter-spacing:.5px}
.powered{position:absolute;left:0;top:321px;width:514px;text-align:center;font-size:12px;color:var(--ink)}
.powered-name{position:absolute;left:0;top:350px;width:514px;text-align:center;font-size:15px;font-weight:700;color:var(--ink)}

/* welcome */
.welcome-photo{position:absolute;left:74px;top:715px;width:602px;height:343px;background:linear-gradient(180deg,#5f86b8 0%,#b8c3cf 50%,#5d6e4c 80%,#3f5a33 100%)}
.accent-line{position:absolute;width:3px;background:#111}
.welcome-card{position:absolute;left:497px;top:743px;width:629px;height:376px;background:var(--card-bg);box-shadow:0 4px 16px rgba(0,0,0,.22)}
.welcome-kicker{position:absolute;left:31px;top:35px;font-size:23px;font-weight:400;color:var(--ink)}
.welcome-title{position:absolute;left:31px;top:62px;font-size:33px;font-weight:400;color:var(--ink)}
.welcome-text{position:absolute;left:31px;top:113px;width:570px;font-size:14.5px;line-height:26px;color:var(--muted)}
.btn-read{position:absolute;left:32px;top:297px;width:147px;height:38px;background:var(--btn);font-size:14px;line-height:38px;text-align:center;color:var(--ink);text-transform:uppercase}

/* featured */
.featured-band{position:absolute;left:0;top:1181px;width:1200px;height:629px}
.featured-title{position:absolute;left:0;top:1254px;width:1200px;text-align:center;font-size:31px;font-weight:400;color:#aeb5c3;letter-spacing:1px}
.prop-card{position:absolute;top:1326px;width:331px;height:377px;background:#e4e6eb}
.prop-photo{position:absolute;left:9px;top:9px;width:313px;height:191px}
.prop-name{position:absolute;left:15px;top:222px;font-size:20px;font-weight:400;text-transform:uppercase;color:var(--ink)}
.prop-desc{position:absolute;left:15px;top:251px;width:290px;font-size:13.5px;line-height:24px;color:var(--muted)}
.prop-meta{position:absolute;left:15px;top:306px;font-size:12px;line-height:29px;color:var(--ink)}
.prop-price{position:absolute;right:29px;top:319px;font-size:22px;font-weight:700;color:var(--ink)}
.slide-arrow{position:absolute;top:1505px}

/* testimonials */
.testi-photo{position:absolute;left:524px;top:1845px;width:602px;height:345px;background:linear-gradient(180deg,#5a6a86 0%,#8a94a6 45%,#7b6a5c 70%,#4f6a3c 100%)}
.testi-card{position:absolute;left:74px;top:1874px;width:629px;height:372px;background:var(--card-bg);box-shadow:0 4px 16px rgba(0,0,0,.22)}
.testi-title{position:absolute;left:45px;top:35px;font-size:33px;font-weight:400;color:var(--ink)}
.testi-text{position:absolute;left:45px;top:93px;width:555px;font-size:14.3px;line-height:29px;font-style:italic;color:var(--muted)}
.testi-name{position:absolute;left:45px;top:248px;font-size:14px;font-weight:700;text-transform:uppercase;color:var(--ink)}
.testi-nav{position:absolute;top:307px;width:31px;height:31px;border:1.5px solid #222}

/* footer */
.site-footer{position:absolute;left:0;top:2301px;width:1200px;height:285px;background:var(--footer-bg)}
.footer-brand{position:absolute;left:74px;top:86px;font-size:28px;font-weight:400;letter-spacing:1px;color:#6c6f76;text-transform:uppercase}
.copyright{position:absolute;left:74px;top:156px;font-size:12px;line-height:23px;color:#5c5f66}
.f-head{position:absolute;top:50px;font-size:13px;color:var(--footer-head);text-transform:uppercase;letter-spacing:.5px}
.sitemap{position:absolute;left:374px;top:82px;list-style:none}
.sitemap li{font-size:12.5px;line-height:31.5px;color:var(--footer-text)}
.contact-name{position:absolute;left:614px;top:93px;font-size:12.5px;color:var(--footer-head);text-transform:uppercase}
.contact-row{position:absolute;left:614px;font-size:12.5px;line-height:21px;color:var(--footer-text)}
.contact-row svg{position:absolute;left:0;top:3px}
.contact-row span{display:block;margin-left:34px}
.sub-input{position:absolute;left:884px;top:87px;width:202px;height:38px;background:#fff;font-size:12.5px;line-height:38px;padding-left:12px;color:#333}
.sub-go{position:absolute;left:1086px;top:87px;width:40px;height:38px;background:#c8cdd8;font-size:13px;font-weight:700;line-height:38px;text-align:center;color:#222}
.social{position:absolute;top:199px;width:20px;height:20px;border-radius:50%;background:#5d6068}
</style>
</head>
<body>

<header class="site-header">
  <div class="brand">Hearthline</div>
  <nav class="main-nav">
    <a class="active" style="left:521px">Home</a>
    <a style="left:619px">Qeno Info</a>
    <a style="left:729px">About Qe No Home</a>
    <a style="left:908px">Downloads</a>
    <a style="left:1036px">Contact Us</a>
  </nav>
</header>

<section class="hero" role="img" aria-label="Two-storey brick family home with lawn and trees at dusk">
  <h1 class="hero-title">HEARTHLINE REALTY GROUP</h1>
  <p class="hero-sub">We are your guide from search to keys</p>
</section>

<div class="popup">
  <div class="popup-fade" role="img" aria-label="Faded lakeside house photograph"></div>
  <div class="popup-close">X</div>
  <h2 class="popup-title">My Free Market Analysis</h2>
  <div class="field" style="left:17px;top:87px;width:230px">Full Name</div>
  <div class="field" style="left:264px;top:87px;width:229px">Phone Number</div>
  <div class="field" style="left:17px;top:133px;width:476px">Email Address</div>
  <div class="field" style="left:17px;top:181px;width:476px">Address</div>
  <div class="submit">SUBMIT</div>
  <div class="powered">Powered by</div>
  <div class="powered-name">Postwing</div>
</div>

<section class="welcome">
  <div class="welcome-photo" role="img" aria-label="Large white lakefront home with gabled roofs and deck"></div>
  <div class="accent-line" style="left:114px;top:760px;height:248px"></div>
  <div class="accent-line" style="left:120px;top:770px;height:220px;width:2px"></div>
  <div class="welcome-card">
    <div class="welcome-kicker">WELCOME TO</div>
    <h2 class="welcome-title">HEARTHLINE REALTY GROUP</h2>
    <p class="welcome-text">Lorem ipsum dolor sit amet, consectetur adipisicing elit, sed do eiusmod tempor incididunt ut labore et doloreasdes magna aliqua. Ut enim ad minim veniam, quis nostrud exercitation ullamco laboris nisi ut aliquip ex ea commodalo consequat. Duis aute irure dolor in reprehenderit in voluptate velit esse cillum dolore eu fugiat nulla pariatur. Excepteur sint occaecat cupidatat non proident, sunt in culpa qui officia deserunt mollit anim id est laborum.</p>
    <div class="btn-read">Read More</div>
  </div>
</section>

<section class="featured">
  <svg class="featured-band" width="1200" height="629" viewBox="0 0 1200 629" role="img" aria-label="Dusky lake and treeline at evening">
    <defs>
      <linearGradient id="bandFill" x1="0" y1="0" x2="0" y2="1">
        <stop offset="0" stop-color="#232c40"/>
        <stop offset=".55" stop-color="#2e3a4f"/>
        <stop offset="1" stop-color="#1f2a33"/>
      </linearGradient>
    </defs>
    <polygon points="0,34 1200,0 1200,629 0,591" fill="url(#bandFill)"/>
  </svg>
  <h2 class="featured-title">FEATURED PROPERTIES</h2>

  <svg class="slide-arrow" style="left:17px" width="44" height="20" viewBox="0 0 44 20"><path d="M43 10H3M11 2L3 10l8 8" fill="none" stroke="#c9ced8" stroke-width="2"/></svg>
  <svg class="slide-arrow" style="left:1139px" width="44" height="20" viewBox="0 0 44 20"><path d="M1 10h40M33 2l8 8-8 8" fill="none" stroke="#c9ced8" stroke-width="2"/></svg>

  <article class="prop-card" style="left:74px">
    <div class="prop-photo" role="img" aria-label="White estate home among autumn trees" style="background:linear-gradient(180deg,#6c7c5a 0%,#8fa0b0 45%,#4d6a37 100%)"></div>
    <h3 class="prop-name">Name Heading</h3>
    <p class="prop-desc">Ut enim ad minim veniam, quis nostrud exercitation ullamco..</p>
    <div class="prop-meta">Bed : 3 &nbsp;|&nbsp; Bath: 2<br>Area: 1200 Sqft</div>
    <div class="prop-price">$152,20,000</div>
  </article>

  <article class="prop-card" style="left:434px">
    <div class="prop-photo" role="img" aria-label="Stone house with wide front lawn" style="background:linear-gradient(180deg,#3e4b3a 0%,#7a7e78 45%,#4f7a32 100%)"></div>
    <h3 class="prop-name">Name Heading</h3>
    <p class="prop-desc">Ut enim ad minim veniam, quis nostrud exercitation ullamco..</p>
    <div class="prop-meta">Bed : 3 &nbsp;|&nbsp; Bath: 2<br>Area: 1200 Sqft</div>
    <div class="prop-price">$152,20,000</div>
  </article>

  <article class="prop-card" style="left:795px">
    <div class="prop-photo" role="img" aria-label="Lake house with boathouse on the water" style="background:linear-gradient(180deg,#4b6a4a 0%,#c7ccd0 40%,#3b5f82 75%,#2c4a6a 100%)"></div>
    <h3 class="prop-name">Name Heading</h3>
    <p class="prop-desc">Ut enim ad minim veniam, quis nostrud exercitation ullamco..</p>
    <div class="prop-meta">Bed : 3 &nbsp;|&nbsp; Bath: 2<br>Area: 1200 Sqft</div>
    <div class="prop-price">$152,20,000</div>
  </article>
</section>

<section class="testimonials">
  <div class="testi-photo" role="img" aria-label="Family standing in front of their blue-sided home"></div>
  <div class="accent-line" style="left:1079px;top:1888px;height:250px"></div>
  <div class="accent-line" style="left:1085px;top:1900px;height:228px;width:2px"></div>
  <div class="testi-card">
    <h2 class="testi-title">TESTIMONIALS</h2>
    <p class="testi-text">Lorem ipsum dolor sit amet, consectetur adipisicing elit, sed do eiusmod tempor incididunt ut labore et doloreasdes magna aliqua. Ut enim ad minim veniam, quis nostrud exercitation ullamco laboris nisi ut aliquip ex ea commodalo consequat irure dolor in reprehenderit in voluptate velit esse cillum dolore eu fugiat nulla pariatur xcepteur sint occaecat cupidatat non proident..”</p>
    <div class="testi-name">Name Heading</div>
    <svg class="testi-nav" style="left:45px" viewBox="0 0 31 31"><path d="M18 9l-6 6.5 6 6.5" fill="none" stroke="#222" stroke-width="2"/></svg>
    <svg class="testi-nav" style="left:90px" viewBox="0 0 31 31"><path d="M13 9l6 6.5-6 6.5" fill="none" stroke="#222" stroke-width="2"/></svg>
  </div>
</section>

<footer class="site-footer">
  <div class="footer-brand">Hearthline</div>
  <p class="copyright">Copyright © 2018 Company Name<br>All Right Reserved</p>

  <div class="f-head" style="left:374px">Site Map</div>
  <ul class="sitemap">
    <li>Home</li><li>Qeno Info</li><li>About Qe No Home</li><li>Downloads</li><li>Contact us</li>
  </ul>

  <div class="f-head" style="left:614px">Contact Info</div>
  <div class="contact-name">Hearthline Realty Group</div>
  <div class="contact-row" style="top:121px">
    <svg width="10" height="14" viewBox="0 0 10 14"><path d="M5 0a5 5 0 0 0-5 5c0 4 5 9 5 9s5-5 5-9a5 5 0 0 0-5-5zm0 7a2 2 0 1 1 0-4 2 2 0 0 1 0 4z" fill="#6a6d74"/></svg>
    <span>14 Maple Court, Lakeview<br>City, USA</span>
  </div>
  <div class="contact-row" style="top:173px">
    <svg width="12" height="12" viewBox="0 0 12 12"><path d="M2.4 0l2 3-1.3 1.4a7 7 0 0 0 4.5 4.5L9 7.6l3 2-1.3 2.4C5 12 0 7 0 1.3z" fill="#6a6d74"/></svg>
    <span>1-800-555-0142</span>
  </div>
  <div class="contact-row" style="top:204px">
    <svg width="13" height="10" viewBox="0 0 13 10"><path d="M0 0h13v10H0z" fill="#6a6d74"/><path d="M0 0l6.5 5L13 0" fill="none" stroke="#121214" stroke-width="1.2"/></svg>
    <span>info@hearthlinegroup.com</span>
  </div>

  <div class="f-head" style="left:886px">Email Subscribe</div>
  <div class="sub-input">Enter Email Address</div>
  <div class="sub-go">GO</div>
  <div class="f-head" style="left:886px;top:160px">Follow Us</div>
  <div class="social" style="left:881px" aria-label="Social link"></div>
  <div class="social" style="left:923px" aria-label="Social link"></div>
  <div class="social" style="left:966px" aria-label="Social link"></div>
  <div class="social" style="left:1009px" aria-label="Social link"></div>
  <div class="social" style="left:1050px" aria-label="Social link"></div>
</footer>

</body>
</html>
```